Healthcare technology firm needs business card layout. Logo provided.

We need a business card design for a new healthcare technology company called BelnaVix.net. The logo is already done so that will be used in the design. We assist patients and their families manage their personal health finances. Our initial product is our web site membership that includes educational content on your health benefits, tools, and downloadable forms.

We would like to see designs that use our existing logo or extend the logo in a creative way. Should be very consumer friendly.

Industry/Entity Type

Healthcare

```html
<!DOCTYPE html>
<html lang="en">
<head>
<meta charset="utf-8">
<title>BelnaVix Business Card</title>
<link rel="stylesheet" href="https://fonts.googleapis.com/css2?family=Questrial&family=Mulish:ital,wght@1,500&display=swap">
<style>
  :root {
    --page-bg: #e9ecef;
    --brand-blue: #1a6fcf;
    --brand-blue-deep: #0b57b8;
    --brand-blue-light: #2f8ee0;
    --ink: #4a4a4a;
    --card-white: #ffffff;
    --band-text: #eaf3ff;
    --icon-green: #3fae49;
  }
  * { margin: 0; padding: 0; box-sizing: border-box; }
  html, body {
    width: 1200px; height: 960px; overflow: hidden;
    background: var(--page-bg);
    font-family: "Questrial", "Century Gothic", sans-serif;
  }
  .canvas {
    width: 1200px; height: 960px;
    display: flex; flex-direction: column; align-items: center; justify-content: center;
    gap: 40px;
  }
  .card {
    width: 700px; height: 400px; position: relative; overflow: hidden;
    box-shadow: 0 6px 18px rgba(0,0,0,.15);
  }
  /* Front */
  .card-front { background: var(--brand-blue); }
  .front-pattern {
    position: absolute; inset: 0;
    background: linear-gradient(160deg, var(--brand-blue-light) 0%, var(--brand-blue) 55%, var(--brand-blue-deep) 100%);
  }
  .front-wordmark {
    position: absolute; right: 44px; bottom: 120px;
    font-size: 68px; letter-spacing: 1px; color: var(--card-white);
  }
  /* Back */
  .card-back { background: var(--card-white); }
  .back-main { position: absolute; inset: 0 0 70px 0; display: flex; }
  .brand-block { width: 390px; padding: 112px 0 0 42px; }
  .brand-name { font-size: 54px; color: var(--brand-blue); line-height: 1; letter-spacing: 1px; }
  .brand-tagline {
    margin-top: 18px; font-family: "Mulish", sans-serif; font-style: italic; font-weight: 500;
    font-size: 18px; color: var(--brand-blue); white-space: nowrap;
  }
  .divider {
    width: 2px; margin: 52px 0 40px;
    background: linear-gradient(to bottom, transparent, var(--brand-blue), transparent);
  }
  .contact-block { padding: 70px 0 0 50px; color: var(--ink); }
  .person-name { font-size: 25px; letter-spacing: 1px; }
  .person-title { font-size: 25px; letter-spacing: 1px; }
  .contact-list { list-style: none; margin-top: 26px; }
  .contact-item { display: flex; align-items: center; gap: 16px; font-size: 20px; letter-spacing: 1px; margin-bottom: 8px; }
  .contact-icon { width: 20px; height: 20px; flex: none; }
  .location-band {
    position: absolute; left: 0; right: 0; bottom: 0; height: 70px;
    background: linear-gradient(to bottom, var(--brand-blue-light), var(--brand-blue-deep));
    display: flex; align-items: center; justify-content: center; gap: 18px;
    color: var(--band-text); font-size: 21px; letter-spacing: 1px;
  }
  .location-sep { font-size: 14px; }
</style>
</head>
<body>
<main class="canvas">
  <section class="card card-front" aria-label="Business card front">
    <div class="front-pattern" role="img" aria-label="Blue background with repeating concentric circle pattern"></div>
    <div class="front-wordmark">BelnaVix</div>
  </section>

  <section class="card card-back" aria-label="Business card back">
    <div class="back-main">
      <div class="brand-block">
        <div class="brand-name">BelnaVix</div>
        <p class="brand-tagline">Making health costs simple for you</p>
      </div>
      <div class="divider"></div>
      <div class="contact-block">
        <p class="person-name">Marla J. Dorne</p>
        <p class="person-title">CEO</p>
        <ul class="contact-list">
          <li class="contact-item">
            <svg class="contact-icon" viewBox="0 0 20 20" aria-label="Phone">
              <path d="M6 3 L8 7 L6.5 8.5 Q8 12 11.5 13.5 L13 12 L17 14 L16 17 Q9 17.5 3 4 Z" fill="var(--icon-green)"/>
            </svg>
            <span>555-214-7730</span>
          </li>
          <li class="contact-item">
            <svg class="contact-icon" viewBox="0 0 20 20" aria-label="Fax">
              <rect x="5" y="2" width="10" height="5" fill="var(--icon-green)"/>
              <rect x="2" y="7" width="16" height="7" rx="1.5" fill="var(--icon-green)"/>
              <rect x="5" y="12" width="10" height="6" fill="var(--icon-green)" stroke="#fff" stroke-width="1"/>
            </svg>
            <span>555-389-4162</span>
          </li>
        </ul>
      </div>
    </div>
    <div class="location-band">
      <span>Ashford</span><span class="location-sep">●</span>
      <span>Maple Crossing</span><span class="location-sep">●</span>
      <span>Dunmore</span><span class="location-sep">●</span>
      <span>Harlowe</span>
    </div>
  </section>
</main>
</body>
</html>
```